SkyvornQ Business Cards and Stationary Design

Need a design for our business cards and stationary. I want to carry on the theme of the logo. I want the business cards to have a design on the back. I would like the business cards and the stationary to carry the same theme, design scheme, and branding

Target Market(s)

Airlines and Maintenance Facilities

Industry/Entity Type

Aviation

Contact Information for Business Card

Name
Position Title
Address: 4827 Trellis Hollow Road, Fort Pierce, Florida, 34951
Office Number
Mobile Number
Email
Website

Font styles to use
Serif
Sans Serif

Colors

Designer to choose colors to be used in the design.

```html
<!DOCTYPE html>
<html lang="en">
<head>
<meta charset="utf-8">
<title>SkyvornQ Business Card</title>
<link rel="stylesheet" href="https://fonts.googleapis.com/css2?family=Montserrat:wght@400;500;600;700&display=swap">
<style>
  :root {
    --bg: #e9ebee;
    --card: #ffffff;
    --sky: #1fa3dc;
    --navy: #1e2f6b;
    --ink: #1b1d2a;
    --rule: #9fd6ef;
  }
  * { margin: 0; padding: 0; box-sizing: border-box; }
  html, body { width: 1200px; height: 800px; overflow: hidden; }
  body {
    background: var(--bg);
    font-family: "Montserrat", Arial, sans-serif;
    position: relative;
  }
  .card {
    position: absolute;
    top: 278px;
    width: 430px;
    height: 245px;
    background: var(--card);
    box-shadow: 0 6px 18px rgba(0,0,0,0.18);
  }
  .card-front { left: 166px; border-radius: 12px; }
  .card-back { left: 604px; }

  .holder-name {
    position: absolute; left: 20px; top: 27px;
    color: var(--sky); font-size: 19px; font-weight: 500;
  }
  .holder-title {
    position: absolute; left: 20px; top: 55px;
    color: var(--ink); font-size: 11px; font-weight: 600;
  }
  .title-rule {
    position: absolute; left: 20px; top: 75px;
    width: 16px; height: 1px; background: var(--rule);
  }
  .contact-list {
    position: absolute; left: 20px; top: 98px;
    list-style: none; font-size: 11px; line-height: 14px;
    color: var(--ink); font-weight: 500;
  }
  .contact-list .label { color: var(--sky); }
  .address {
    position: absolute; left: 20px; top: 183px;
    font-size: 11px; line-height: 13.5px; color: var(--ink); font-weight: 500;
    font-style: normal;
  }

  .brand-circle {
    position: absolute; left: 14px; top: 2px;
  }
  .brand-name {
    position: absolute; left: 125px; top: 103px;
    color: var(--navy); font-size: 29px; font-weight: 700;
    letter-spacing: 5px;
  }
  .brand-web {
    position: absolute; left: 0; right: 0; top: 196px;
    padding-left: 120px; text-align: center;
    color: var(--navy); font-size: 13px; font-weight: 600;
  }
</style>
</head>
<body>
  <section class="card card-front">
    <h1 class="holder-name">Marcus Delane</h1>
    <p class="holder-title">Co-Owner</p>
    <div class="title-rule"></div>
    <ul class="contact-list">
      <li><span class="label">Mobile:</span> (555) 614-2870</li>
      <li><span class="label">Phone:</span> 555-208-4417</li>
      <li><span class="label">Email:</span> info@skyvornq.com</li>
      <li><span class="label">Web:</span> www.skyvornq.com</li>
    </ul>
    <address class="address">
      4827 Trellis Hollow Road,<br>
      Fort Pierce,<br>
      Florida, 34951
    </address>
  </section>

  <section class="card card-back">
    <svg class="brand-circle" width="100" height="240" viewBox="0 0 100 240" aria-hidden="true">
      <circle cx="50" cy="120" r="42" fill="none" stroke="var(--navy)" stroke-width="7"/>
    </svg>
    <p class="brand-name">SKYVORNQ</p>
    <p class="brand-web">www.skyvornq.com</p>
  </section>
</body>
</html>
```